Redesign two existing website pages and one new landing page for dental office

I need to redesign two webpages on my dental website, the Home page (http://velbridgedental.com) and the Dental Implant Services page (http://www.velbridgedental.com/dental-implant-services) and also create a landing page for the Dental Implant Services page.

Please use the same color scheme, slogans and subtitles for the redesign pages and create a reserved video spot on each page. The video spots should not be too big but not too small either and positioned in a central key location on each of the pages. The final redesigned pages should communicate leadership, confidence and trust.

The new landing page for the Dental implant Services page must not have any hyperlinks on the page and must entice the viewer to give name and email before downloading a "Free" eBook called "Is a Fuller Smile Worth the Wait?" Any added photo images to this new page must be smiling.
Updates

Project Deadline Extended Reason: I got feedback that my project was not long enough so I'm extending it by 5 days. Added Thursday, April 16, 2015

Target Market(s)

People who are middle-age to seniors.

Industry/Entity Type

Dental

Coding

Coded - Design and coding required

Number of Pages Required

3 page

Requirements
Must have
• Compatible with existing website colors and theme.

```html
<!DOCTYPE html>
<html lang="en">
<head>
<meta charset="utf-8">
<title>Velbridge Dental Care</title>
<link rel="stylesheet" href="https://fonts.googleapis.com/css2?family=Open+Sans:wght@400;600;700&family=Roboto:wght@400;500;700&display=swap">
<style>
:root{
  --teal-dark:#2c5c56;
  --teal:#3b8178;
  --teal-mid:#4f968c;
  --teal-light:#7fb6ad;
  --mist:#e9f0ef;
  --ink:#333b3a;
  --muted:#6b7473;
  --white:#ffffff;
  --line:#d5dedd;
}
*{box-sizing:border-box;margin:0;padding:0}
html,body{width:1200px;height:2184px;overflow:hidden}
body{font-family:"Open Sans",Arial,sans-serif;color:var(--ink);background:var(--white)}
h1,h2,h3,h4{font-family:"Roboto",Arial,sans-serif}
.page{width:1200px;height:2184px;position:relative}

/* header */
.site-header{height:120px;display:flex;align-items:center;justify-content:space-between;padding:0 130px 0 100px}
.brand{display:flex;align-items:center;gap:12px;font-family:"Roboto",sans-serif;font-weight:700;font-size:30px;color:var(--teal)}
.brand-mark{width:26px;height:26px;border-radius:50%;background:var(--teal)}
.app-badge{display:flex;align-items:center;gap:12px;font-size:15px;line-height:1.3;color:var(--ink)}
.app-badge .phone-box{width:36px;height:52px;border:3px solid var(--ink);border-radius:6px}

/* nav */
.main-nav{height:42px;background:var(--teal-dark);display:flex;align-items:center;padding-left:118px;gap:0}
.main-nav a{color:var(--white);text-decoration:none;font-size:15px;font-family:"Roboto",sans-serif;padding:0 30px;line-height:42px;text-transform:uppercase}
.main-nav a.active{background:#1e403c}

/* hero */
.hero{height:480px;position:relative;background:linear-gradient(180deg,#6ba89f 0%,#4f9088 55%,#3c7d74 100%);overflow:hidden}
.hero-bg{position:absolute;inset:0}
.hero-copy{position:absolute;left:118px;top:104px;width:560px;color:var(--white)}
.hero-copy h1{font-size:44px;line-height:1.15;font-weight:700}
.hero-copy p{margin-top:18px;font-size:16px;line-height:1.5;opacity:.92}
.btn{display:inline-block;background:var(--teal-dark);color:var(--white);font-family:"Roboto",sans-serif;font-size:16px;padding:14px 30px;border-radius:4px;border:2px solid rgba(255,255,255,.35);text-decoration:none}
.hero-copy .btn{margin-top:34px}
.doctor-photo{position:absolute;right:140px;top:40px;width:330px;height:440px;border-radius:160px 160px 0 0}

/* services */
.services{display:flex;margin-top:40px;padding:0 108px;height:400px}
.service-card{flex:1;padding:18px 26px 24px}
.service-card.light{background:var(--mist)}
.service-card.dark{background:var(--teal-dark);color:var(--white)}
.service-card h2{font-size:30px;font-weight:700}
.service-card h3{font-size:21px;font-weight:400;margin-top:4px}
.service-card.light h3{color:var(--teal)}
.service-photo{height:160px;margin-top:18px;width:100%}
.service-card p{font-size:13px;line-height:1.5;margin-top:14px}
.service-card .btn{margin-top:16px;font-size:14px;padding:8px 16px;border:none}
.service-card.dark .btn{background:var(--white);color:var(--teal-dark)}
.service-card.light .btn{background:var(--teal-dark)}

/* features */
.features{display:flex;justify-content:space-between;padding:0 110px;margin-top:90px;height:340px}
.feature{width:220px}
.feature-photo{width:176px;height:176px;border-radius:50%;margin:0 auto;border:8px solid var(--white);box-shadow:0 0 0 2px var(--line)}
.feature h3{text-align:center;font-size:18px;font-weight:500;margin-top:18px;color:var(--ink)}
.feature ul{list-style:none;margin-top:10px;padding-left:22px}
.feature li{font-size:13px;line-height:1.8;color:var(--muted);position:relative;padding-left:14px}
.feature li::before{content:"";position:absolute;left:0;top:9px;width:6px;height:6px;background:var(--teal);border-radius:50%}

/* band */
.cta-band{background:var(--teal);height:160px;text-align:center;color:var(--white);padding-top:28px}
.cta-band h2{font-size:31px;font-weight:700}
.cta-band .btn{margin-top:22px;background:var(--teal-dark);font-size:16px;padding:12px 30px}

/* columns */
.columns{display:flex;gap:40px;padding:0 110px;margin-top:36px;height:310px}
.col{flex:1}
.col h3{font-size:24px;font-weight:700;color:var(--ink);padding-bottom:10px;border-bottom:2px solid var(--line)}
.col-photo{height:130px;margin-top:16px}
.col p{font-size:13px;line-height:1.5;margin-top:12px;color:var(--muted)}
.posts{list-style:none;margin-top:14px}
.posts li{font-size:14px;line-height:1.3;padding:6px 0 6px 16px;position:relative;color:var(--ink)}
.posts li::before{content:"";position:absolute;left:0;top:12px;width:6px;height:6px;background:var(--teal);border-radius:50%}
.video-spot{height:150px;margin-top:16px;background:linear-gradient(135deg,#2d3a3a,#56706c);position:relative}
.video-spot svg{position:absolute;left:50%;top:50%;transform:translate(-50%,-50%)}

/* footer */
.site-footer{position:absolute;left:0;right:0;bottom:0;height:160px;background:var(--teal-dark);color:var(--white);text-align:center;padding-top:16px}
.footer-phone{display:flex;justify-content:center;align-items:center;gap:12px;font-family:"Roboto",sans-serif;font-size:28px;font-weight:500}
.footer-links{margin-top:10px;font-size:14px}
.footer-links a{color:var(--white);text-decoration:none;padding:0 8px}
.socials{display:flex;justify-content:center;gap:10px;margin-top:12px}
.socials span{width:28px;height:28px;background:var(--white);border-radius:3px;opacity:.85}
.copyright{font-size:12px;margin-top:12px;opacity:.85}
</style>
</head>
<body>
<div class="page">
  <header class="site-header">
    <div class="brand"><span class="brand-mark"></span>Velbridge Dental Care</div>
    <div class="app-badge"><span class="phone-box"></span><span>Get Dr. Vale's<br>Mobile App</span></div>
  </header>

  <nav class="main-nav">
    <a class="active" href="#">Home</a>
    <a href="#">About Us</a>
    <a href="#">Dental Services</a>
    <a href="#">Blog</a>
    <a href="#">Contact Us</a>
    <a href="#">Testimonials</a>
  </nav>

  <section class="hero">
    <div class="hero-bg" role="img" aria-label="Softly blurred dental office interior in teal tones"></div>
    <div class="hero-copy">
      <h1>Life-Changing Family Dental<br>Care In Maple Hollow</h1>
      <p>In this warm office we help every patient smile with comfort, trust and care that lasts for years.</p>
      <a class="btn" href="#">Appointment</a>
    </div>
    <div class="doctor-photo" role="img" aria-label="Smiling dentist in a white coat with arms crossed" style="background:linear-gradient(180deg,#dfe9e7 0%,#c9d6d4 60%,#f4f6f6 100%)"></div>
  </section>

  <section class="services">
    <article class="service-card light">
      <h2>Dental Hygiene Services</h2>
      <h3>Achieve Better Health With Prevention</h3>
      <div class="service-photo" role="img" aria-label="Smiling woman brushing her teeth" style="background:linear-gradient(90deg,#f3f0ec,#d9e4e2)"></div>
      <p>Maintain healthy teeth and gums with consistent dental exams and tooth cleanings by one of our professional dental hygienists.</p>
      <a class="btn" href="#">Learn More</a>
    </article>
    <article class="service-card dark">
      <h2>Dental Emergency Services</h2>
      <h3>Stop Pain From Tooth Trauma and Infection</h3>
      <div class="service-photo" role="img" aria-label="Patient receiving a dental check-up with instruments" style="background:linear-gradient(90deg,#d8e3e2,#f0ebe6)"></div>
      <p>Maintain healthy teeth and gums with consistent dental exams and tooth cleanings by one of our professional dental hygienists.</p>
      <a class="btn" href="#">Learn More</a>
    </article>
  </section>

  <section class="features">
    <div class="feature">
      <div class="feature-photo" role="img" aria-label="Smiling senior couple" style="background:linear-gradient(135deg,#e6ddd3,#b9cbc8)"></div>
      <h3>Beautiful Dentures</h3>
      <ul><li>What is a Denture?</li><li>Who Needs a Denture?</li><li>Just How Are Dentures Made?</li></ul>
    </div>
    <div class="feature">
      <div class="feature-photo" role="img" aria-label="Smiling young couple" style="background:linear-gradient(135deg,#ecd9cc,#c3d3d0)"></div>
      <h3>Cosmetic Dentistry</h3>
      <ul><li>What is a Denture?</li><li>Who Needs a Denture?</li><li>Just How Are Dentures Made?</li></ul>
    </div>
    <div class="feature">
      <div class="feature-photo" role="img" aria-label="Close-up of a dental implant model" style="background:linear-gradient(135deg,#e9c7c4,#d8dedd)"></div>
      <h3>Dental Implant Services</h3>
      <ul><li>What is a Denture?</li><li>Who Needs a Denture?</li><li>Just How Are Dentures Made?</li></ul>
    </div>
    <div class="feature">
      <div class="feature-photo" role="img" aria-label="Relaxed patient in a dental chair" style="background:linear-gradient(135deg,#dfe6e5,#aac6c1)"></div>
      <h3>Sedation Dentistry</h3>
      <ul><li>Control Dental Fear</li><li>Dental Pain Management</li><li>Relaxed and Tranquil</li></ul>
    </div>
  </section>

  <section class="cta-band">
    <h2>Comprehensive Family Dentistry in One Maple Hollow Dental Office!</h2>
    <a class="btn" href="#">Schedule An Appointment?</a>
  </section>

  <section class="columns">
    <div class="col">
      <h3>Don't Wait 'til it Hurts!</h3>
      <div class="col-photo" role="img" aria-label="Smiling woman holding her cheek" style="background:linear-gradient(90deg,#efe8e1,#d4e0de)"></div>
      <p>Get acquainted today with comfortable dental care. Request an appointment now and we will contact you right away to schedule your dental visit!</p>
    </div>
    <div class="col">
      <h3>Recent Blog Posts</h3>
      <ul class="posts">
        <li>Conscious Sedation: A Way to Deal with Anxiety at the Dentist's Office</li>
        <li>Pediatric Dentists and Their Importance in Today's World</li>
        <li>Tooth Implant Facts</li>
        <li>Is Sedation Dentistry Cost Affordable?</li>
        <li>How to Prepare for Oral Surgery</li>
      </ul>
    </div>
    <div class="col">
      <h3>Dr. Elias Vale</h3>
      <div class="video-spot" role="img" aria-label="Video introduction from the dentist">
        <svg width="56" height="56" viewBox="0 0 56 56"><circle cx="28" cy="28" r="27" fill="rgba(255,255,255,.25)"/><path d="M22 17 L40 28 L22 39 Z" fill="#fff"/></svg>
      </div>
    </div>
  </section>

  <footer class="site-footer">
    <div class="footer-phone">
      <svg width="30" height="30" viewBox="0 0 30 30"><circle cx="15" cy="15" r="14" fill="none" stroke="#fff" stroke-width="2"/><path d="M10 8c1-1 2 0 3 2s0 2-1 3c1 2 3 4 5 5 1-1 1-2 3-1s3 2 2 3c-1 2-3 3-6 1-3-2-5-4-7-7-2-3-0-5 1-6z" fill="#fff"/></svg>
      (281) 555-0142
    </div>
    <div class="footer-links"><a href="#">Home</a>|<a href="#">About Us</a>|<a href="#">Dental Services</a>|<a href="#">Blog</a>|<a href="#">Contact Us</a>|<a href="#">Testimonials</a></div>
    <div class="socials"><span></span><span></span><span></span><span></span><span></span></div>
    <div class="copyright">©2014 Velbridge Dental Care, Harbor Crest Medical Center, 4120 Harbor Crest Blvd, Ste. 210, Maple Hollow, TX 77000</div>
  </footer>
</div>
</body>
</html>
```